Glen Whitmore Professional Coaching

I would like a website with a mountain theme geared towards professional executives reaching higher peaks and goals. This is a 3 page website with brand essence information on the opening page, the coaching process on a second page and "about me" and lead capture form on a third page

Target Market(s)

C-Level audience, involved in tech, government, manufacturing, and transportation type of corporations

Coding

Coded - Design and coding required

Number of Pages Required

3 page

Font styles to use
Sans Serif

Colors
a7a7a7
1b1b1b
e8e8e8
3176b5
abd036
0355a3

Requirements
Must have
• Looking for a user friendly site that I can manage/update going forward. Must have:
• 1. "Is coaching right for you?" - page 1
• 2. "Our Process" page 2 - I will describe how we approach coaching
• 3. "Contact us" page 3 where I can capture contact information from potential clients
• 4. Clean and professional with more modern font
• 5. Links to personal social media sites
• 6. Ability to upload/download .pdf documents as resources
• 7. Ability to add on new pages in the future (such as a blog page)
Nice to have
• I want a place to store articles I write or use.
• LinkedIn or Twitter Feed
Should not have
• Not fluffy or too 'zen' like personal life coaches tend to present.

```html
<!DOCTYPE html>
<html lang="en">
<head>
<meta charset="utf-8">
<title>Glen Whitmore Professional Coaching</title>
<link href="https://fonts.googleapis.com/css2?family=Poppins:wght@500;600;700;800&family=PT+Sans:wght@400;700&display=swap" rel="stylesheet">
<style>
:root{
  --ink:#1b1b1b;
  --ink-soft:#3a3a3a;
  --text:#4a4a4a;
  --muted:#a7a7a7;
  --page:#f3f2f7;
  --line:#e8e8e8;
  --blue:#1684cf;
  --blue-deep:#0355a3;
  --blue-mid:#3176b5;
  --white:#ffffff;
}
*{margin:0;padding:0;box-sizing:border-box}
html,body{width:1200px;height:4000px;overflow:hidden}
body{position:relative;background:var(--page);font-family:"PT Sans",Arial,sans-serif;color:var(--text)}
.abs{position:absolute}
.btn{position:absolute;background:var(--blue);color:var(--white);font-family:"Poppins",Arial,sans-serif;font-weight:700;text-transform:uppercase;display:flex;align-items:center;justify-content:center;letter-spacing:.5px}

/* hero */
.hero{left:0;top:0;width:1200px;height:701px;background:linear-gradient(180deg,#eef3fb 0%,#c9d8ee 28%,#7d9fcf 52%,#2f5b9e 75%,#1a3b72 100%)}
.brand{left:40px;top:28px;font-family:"Poppins",Arial,sans-serif;font-weight:700;font-size:24px;color:var(--ink)}
.nav{right:40px;top:30px;display:flex;gap:40px;font-family:"Poppins",Arial,sans-serif;font-weight:600;font-size:15px;color:var(--ink)}
.hero-title{left:0;width:1200px;top:208px;text-align:center;font-family:"Poppins",Arial,sans-serif;font-weight:800;font-size:62px;line-height:62px;color:#2a2a2a}
.dots{left:553px;top:646px;display:flex;gap:12px}
.dots span{width:8px;height:8px;border-radius:50%;background:var(--white);opacity:.9}

/* services */
.section-title{left:0;width:1200px;text-align:center;font-family:"Poppins",Arial,sans-serif;font-weight:700;color:var(--ink)}
.rule{left:585px;width:30px;height:3px;background:var(--muted)}
.service{width:300px;text-align:center}
.service .icon{width:124px;height:124px;margin:0 auto;border:3px solid var(--blue);border-radius:50%;display:flex;align-items:center;justify-content:center}
.service h3{margin-top:50px;font-family:"Poppins",Arial,sans-serif;font-weight:700;font-size:19px;color:var(--ink)}
.service p{margin:18px auto 0;width:240px;font-size:15px;line-height:18px;color:var(--text)}
.service .btn{position:static;margin:25px auto 0;width:96px;height:26px;font-size:11px}
.ridge{left:0;top:1245px;width:1200px;height:250px;background:linear-gradient(180deg,#f3f2f7 0%,#c7d6ea 30%,#8eabd0 55%,#dfe6f1 80%,#f3f2f7 100%)}

/* welcome */
.portrait{left:0;top:1533px;width:645px;height:587px;background:radial-gradient(ellipse at 45% 50%,#6f8e5a 0%,#3f6a3a 45%,#2b3f2c 100%);border-radius:0 40px 60px 0}
.welcome-tag{left:581px;top:1558px;width:176px;height:34px;background:var(--blue-mid);color:var(--white);font-family:"Poppins",Arial,sans-serif;font-weight:700;font-size:20px;display:flex;align-items:center;justify-content:center}
.welcome-name{left:586px;top:1596px;font-family:"Poppins",Arial,sans-serif;font-weight:800;font-size:50px;color:#7f95ac;letter-spacing:1px}
.welcome-copy{left:696px;top:1718px;width:360px;font-size:15px;line-height:18.6px;color:var(--text)}
.diagonal{left:0;top:1990px;width:1200px;height:240px}

/* change */
.benefit{width:226px;text-align:center}
.benefit h4{margin-top:14px;font-family:"Poppins",Arial,sans-serif;font-weight:600;font-size:15px;line-height:19px;color:var(--ink-soft)}
.divider{width:1px;height:170px;top:2330px;background:#d5d5dc}

/* cta */
.cta{left:0;top:2547px;width:1200px;height:520px;background:linear-gradient(180deg,#3a2e2a 0%,#7a4a32 18%,#4a3328 40%,#231b19 70%,#141212 100%)}
.cta-title{left:0;width:1200px;top:2750px;text-align:center;font-family:"Poppins",Arial,sans-serif;font-weight:700;font-size:32px;color:var(--white)}
.cta-copy{left:330px;width:540px;top:2816px;text-align:center;font-size:19px;line-height:26px;color:#eaeaea}

/* contact */
.contact-title{left:237px;top:3122px;font-family:"Poppins",Arial,sans-serif;font-weight:700;font-size:38px;color:var(--ink)}
.field{background:var(--white);border:1px solid #cfcfd6;font-size:11px;color:var(--ink-soft);padding:12px 14px;text-transform:uppercase;letter-spacing:.5px}

/* footer */
.footer{left:0;top:3560px;width:1200px;height:440px;background:linear-gradient(180deg,#f3f2f7 0%,#a9d6ee 18%,#5fb1de 40%,#1f86c7 65%,#0c5f9f 100%)}
.footer-name{left:0;width:1200px;top:3715px;text-align:center;font-family:"Poppins",Arial,sans-serif;font-weight:800;font-size:36px;color:var(--white)}
.footer-nav{left:0;width:1200px;top:3799px;display:flex;justify-content:center;gap:22px;font-family:"Poppins",Arial,sans-serif;font-weight:600;font-size:13px;color:var(--white)}
.footer-nav span.sep{opacity:.7}
.follow{left:500px;top:3855px;display:flex;align-items:center;gap:12px;font-family:"Poppins",Arial,sans-serif;font-weight:600;font-size:13px;color:var(--white)}
.follow i{display:block;width:24px;height:24px;border-radius:50%;background:var(--blue-deep)}
.copyright{left:0;width:1200px;top:3922px;text-align:center;font-size:12px;color:var(--white)}
</style>
</head>
<body>

<div class="abs hero" role="img" aria-label="Hiker standing on a rocky summit facing snowy mountain peaks"></div>
<div class="abs brand">GLEN WHITMORE</div>
<nav class="abs nav"><span>HOME</span><span>ABOUT ME</span><span>COACHING PROCESS</span></nav>
<h1 class="abs hero-title">PROFESSIONAL<br>COACHING</h1>
<div class="abs dots"><span></span><span></span><span></span><span></span><span></span></div>

<h2 class="abs section-title" style="top:752px;font-size:36px">SERVICES</h2>
<div class="abs rule" style="top:808px"></div>

<div class="abs service" style="left:122px;top:876px">
  <div class="icon"><svg width="58" height="50" viewBox="0 0 58 50" fill="none" stroke="#1684cf" stroke-width="3"><rect x="3" y="12" width="52" height="35" rx="4"/><path d="M20 12V5h18v7M3 26h52"/></svg></div>
  <h3>Executive Coaching</h3>
  <p>Sed ut perspiciatis unde omnis iste natus error sit voluptatem accusa ntium doloremque lauda ntium, totam rem aperiam eaque ipsa quae.</p>
  <div class="btn">Read More</div>
</div>
<div class="abs service" style="left:447px;top:876px">
  <div class="icon"><svg width="64" height="56" viewBox="0 0 64 56" fill="none" stroke="#1684cf" stroke-width="2.5"><circle cx="32" cy="10" r="7"/><path d="M22 30c0-7 4-11 10-11s10 4 10 11"/><circle cx="14" cy="36" r="6"/><circle cx="32" cy="36" r="6"/><circle cx="50" cy="36" r="6"/><path d="M4 54c0-6 4-9 10-9s10 3 10 9M22 54c0-6 4-9 10-9s10 3 10 9M40 54c0-6 4-9 10-9s10 3 10 9"/></svg></div>
  <h3>Leadership Development</h3>
  <p>Sed ut perspiciatis unde omnis iste natus error sit voluptatem accusa ntium doloremque lauda ntium, totam rem aperiam eaque ipsa quae.</p>
  <div class="btn">Read More</div>
</div>
<div class="abs service" style="left:778px;top:876px">
  <div class="icon"><svg width="64" height="58" viewBox="0 0 64 58" fill="none" stroke="#1684cf" stroke-width="2.5"><rect x="6" y="4" width="52" height="34"/><path d="M12 30l10-10 8 6 12-12 8 6M32 38v8M20 56l12-10 12 10"/></svg></div>
  <h3>Workshops &amp; Facilitation</h3>
  <p>Sed ut perspiciatis unde omnis iste natus error sit voluptatem accusa ntium doloremque lauda ntium, totam rem aperiam eaque ipsa quae.</p>
  <div class="btn">Read More</div>
</div>

<div class="abs ridge" role="img" aria-label="Snow covered mountain range rising above clouds"></div>

<div class="abs portrait" role="img" aria-label="Portrait of the coach in a navy blazer against green foliage"></div>
<div class="abs welcome-tag">WELCOME TO</div>
<div class="abs welcome-name">GLEN WHITMORE</div>
<p class="abs welcome-copy">At vero eos et accusamus et iusto odio dignissimos ducimus qui blanditiis praesentium voluptatum deleniti atque corrupti quos dolores et quas molestias excepturi sint occaecati cupiditate non provident, similique sunt in culpa qui officia deserunt mollitia animi, id est laborum et dolorum fuga. Et harum quidem rerum facilis est et expedita distinctio. Nam libero tempore, cum soluta nobis est eligendi optio cumque nihil impedit.</p>
<div class="btn" style="left:701px;top:1953px;width:118px;height:34px;font-size:13px">Read More</div>

<svg class="abs diagonal" viewBox="0 0 1200 240" preserveAspectRatio="none" aria-hidden="true"><polygon points="0,0 1200,80 1200,240 0,240" fill="#eeedf3"/></svg>

<h2 class="abs section-title" style="top:2222px;font-size:36px">POWERFUL POSITIVE CHANGE</h2>

<div class="abs benefit" style="left:146px;top:2352px">
  <svg width="56" height="54" viewBox="0 0 56 54" fill="none" stroke="#1684cf" stroke-width="2.5"><circle cx="20" cy="13" r="9"/><circle cx="38" cy="13" r="9"/><path d="M4 50c0-12 7-20 16-20s16 8 16 20zM34 30c9 0 18 6 18 20H40"/></svg>
  <h4>Improved<br>Leadership Capacity</h4>
</div>
<div class="abs divider" style="left:389px"></div>
<div class="abs benefit" style="left:370px;top:2352px">
  <svg width="56" height="54" viewBox="0 0 56 54" fill="none" stroke="#1684cf" stroke-width="2.5"><circle cx="28" cy="24" r="8"/><path d="M14 50c0-9 6-14 14-14s14 5 14 14M28 4v5M12 10l4 4M44 10l-4 4M6 24h5M45 24h5"/></svg>
  <h4>Increase<br>Self Esteem</h4>
</div>
<div class="abs divider" style="left:595px"></div>
<div class="abs benefit" style="left:596px;top:2352px">
  <svg width="56" height="54" viewBox="0 0 56 54" fill="none" stroke="#1684cf" stroke-width="2.5"><path d="M4 50h48M10 50V38h7v12M22 50V30h7v12M34 50V22h7v28M46 50V14"/><path d="M8 28l14-10 10 6 16-16M40 8h8v8"/></svg>
  <h4>Growth<br>Performance</h4>
</div>
<div class="abs divider" style="left:821px"></div>
<div class="abs benefit" style="left:828px;top:2352px">
  <svg width="56" height="54" viewBox="0 0 56 54" fill="none" stroke="#1684cf" stroke-width="2.5"><path d="M20 36c0-6-8-9-8-18a16 16 0 0 1 32 0c0 9-8 12-8 18zM21 42h14M23 48h10"/></svg>
  <h4>Creating a Culture<br>of Inspiration &amp; Re<br>Imagination</h4>
</div>

<div class="abs cta" role="img" aria-label="Layered mountain ridges at dusk in warm brown tones"></div>
<h2 class="abs cta-title">Ready To Take It To The Next Level?</h2>
<p class="abs cta-copy">At vero eos et accusamus et iusto odio dignissimos ducimus blanditiis praesentium voluptatum deleniti atque</p>
<div class="btn" style="left:496px;top:2906px;width:208px;height:44px;font-size:15px">Contact Us Today</div>

<h2 class="abs contact-title">CONTACT ME</h2>
<div class="abs field" style="left:240px;top:3200px;width:232px;height:44px">Name</div>
<div class="abs field" style="left:485px;top:3200px;width:233px;height:44px">E Mail</div>
<div class="abs field" style="left:730px;top:3200px;width:230px;height:44px">Phone</div>
<div class="abs field" style="left:240px;top:3264px;width:720px;height:164px">Message</div>
<div class="btn" style="left:818px;top:3459px;width:142px;height:42px;font-size:19px;text-transform:uppercase">Submit</div>

<div class="abs footer" role="img" aria-label="Misty blue mountain ranges fading into the distance"></div>
<div class="abs footer-name">GLEN WHITMORE</div>
<nav class="abs footer-nav"><span>HOME</span><span class="sep">\</span><span>ABOUT ME</span><span class="sep">\</span><span>COACHING PROCESS</span><span class="sep">\</span><span>CONTACT</span></nav>
<div class="abs follow"><span style="margin-right:14px">FOLLOW</span><i aria-label="Social link one"></i><i aria-label="Social link two"></i><i aria-label="Social link three"></i></div>
<div class="abs copyright">Copyrights @ 2019 All Rights Reserved</div>

</body>
</html>
```